Larkfield Ridge Management

I need a professional website. My current website is larkfieldridgemanagement.com and I hate it. It was created with some AI tool very quickly because I needed a site up and running with no advanced notice. I’m open to all designs .. I trust you, the professionals will deliver the results I’m anxiously awaiting! :)

```html
<!DOCTYPE html>
<html lang="en">
<head>
<meta charset="utf-8">
<title>Larkfield Ridge Management</title>
<link href="https://fonts.googleapis.com/css2?family=Manrope:wght@400;500;600;700;800&display=swap" rel="stylesheet">
<style>
:root{
  --navy:#1f3461;
  --navy-deep:#182a50;
  --red:#d5252a;
  --ink:#333845;
  --muted:#6a6f7a;
  --soft:#eef1f6;
  --star:#f08a1c;
  --white:#fff;
}
*{box-sizing:border-box;margin:0;padding:0}
html,body{width:1200px;height:4003px;overflow:hidden}
body{font-family:"Manrope",sans-serif;color:var(--ink);background:var(--white);position:relative}
.abs{position:absolute}
.eyebrow{color:var(--red);font-size:14px;font-weight:600;letter-spacing:2px;text-transform:uppercase}
.section-title{color:var(--navy);font-weight:800;font-size:40px;line-height:1.15;text-transform:uppercase}
.rule{height:4px;width:72px;background:var(--red);border-radius:2px}
.btn{display:flex;align-items:center;justify-content:center;gap:8px;background:var(--red);color:var(--white);font-weight:700;font-size:14px;text-transform:uppercase;text-decoration:none}

/* header */
.site-header{top:0;left:0;width:1200px;height:87px;background:var(--white);z-index:3}
.brand-tag{left:140px;top:10px;width:150px;height:140px;background:var(--white);display:flex;flex-direction:column;align-items:center;justify-content:center;gap:8px;z-index:4;border-radius:0 0 8px 8px}
.brand-tag .mark{width:22px;height:22px;background:var(--red)}
.brand-tag span{color:var(--navy);font-weight:800;font-size:16px;text-align:center;line-height:1.2}
.nav{top:38px;display:flex;font-size:13px;font-weight:600;color:var(--navy)}
.nav a{color:var(--navy);text-decoration:none;position:absolute;white-space:nowrap}
.nav a.active::before{content:"";position:absolute;left:-6px;right:-6px;top:-38px;height:4px;background:var(--red)}
.phone{left:966px;top:36px;color:var(--navy);font-weight:700;font-size:17px;display:flex;align-items:center;gap:6px}

/* hero */
.hero{top:87px;left:0;width:1200px;height:600px;background:linear-gradient(100deg,#3a4766 0%,#5a6682 40%,#8a7f88 70%,#b38f7f 100%)}
.hero h1{left:113px;top:150px;color:var(--white);font-size:46px;line-height:56px;font-weight:500;text-transform:uppercase}
.hero h1 b{font-weight:800}
.hero p{left:119px;top:284px;width:440px;color:var(--white);font-size:18px;line-height:20px}
.hero .btn{left:117px;top:368px;width:186px;height:44px}

/* services */
.services-head{top:770px;left:0;width:1200px;text-align:center}
.services-head .rule{margin:10px auto 0}
.card{top:914px;height:304px;width:260px;display:flex;align-items:flex-end;justify-content:center;padding-bottom:20px;color:var(--white);font-weight:700;letter-spacing:2px;font-size:16px}
.card-img{background:linear-gradient(160deg,#8a7a6e,#3c4a66)}
.card-img.c3{background:linear-gradient(160deg,#cfc9c2,#5a5f70)}
.card-img.c4{background:linear-gradient(160deg,#4c5262,#9ea4ae)}
.card.featured{top:893px;height:347px;left:342px;width:259px;background:var(--red);flex-direction:column;justify-content:flex-start;align-items:center;padding:76px 20px 0;text-align:center}
.card.featured h3{font-size:18px;letter-spacing:2px;font-weight:700}
.card.featured p{font-size:11px;line-height:17px;letter-spacing:0;font-weight:400;margin-top:10px}
.card.featured .more{margin-top:14px;background:var(--navy);width:142px;height:34px;font-size:12px;letter-spacing:0}

/* about */
.about-ring{left:75px;top:1342px;width:512px;height:512px;border-radius:50%;border:8px solid var(--red);border-right-color:transparent;transform:rotate(20deg)}
.about-photo{left:91px;top:1358px;width:480px;height:480px;border-radius:50%;background:linear-gradient(150deg,#6f8a60,#b7b3a8 55%,#8a6a4e)}
.about-eyebrow{left:643px;top:1408px;display:flex;align-items:center;gap:10px}
.about-eyebrow i{display:block;width:40px;height:2px;background:var(--red)}
.about h2{left:643px;top:1440px;font-size:36px;line-height:46px}
.about .rule{left:645px;top:1539px}
.about p{left:647px;top:1570px;width:480px;font-size:15.5px;line-height:23.5px;color:var(--ink)}
.about .btn{left:643px;top:1719px;width:187px;height:43px}

/* why choose */
.why-head{top:1926px;left:0;width:1200px;text-align:center}
.why-head .eyebrow{display:flex;align-items:center;justify-content:center;gap:10px}
.why-head .eyebrow i{width:38px;height:2px;background:var(--red);display:block}
.why-head h2{margin-top:6px}
.why-head .rule{margin:8px auto 0}
.emblem{left:482px;top:2095px;width:276px;height:286px;display:flex;align-items:center;justify-content:center}
.emblem .plate{width:230px;height:230px;border:6px solid var(--navy);display:flex;flex-direction:column;align-items:center;justify-content:center;gap:14px;text-align:center}
.emblem .plate i{width:34px;height:34px;background:var(--red);display:block}
.emblem .plate span{color:var(--navy);font-weight:800;font-size:24px;line-height:1.2}
.feature h4{font-size:16px;font-weight:600;color:var(--ink);line-height:22px}
.feature p{font-size:11.5px;line-height:17px;color:var(--muted);margin-top:8px}
.feature.left{text-align:right;width:240px}
.feature.right{width:240px}
.icon-box{width:81px;height:78px;display:flex;align-items:center;justify-content:center}
.icon-box.navy{background:var(--navy)}
.icon-box.red{background:var(--red)}
.divider{height:1px;background:#c9ccd3}
.why .btn{left:514px;top:2416px;width:199px;height:41px;clip-path:polygon(8% 0,92% 0,100% 50%,92% 100%,8% 100%,0 50%);font-size:13px}

/* testimonials */
.testimonials{top:2567px;left:0;width:1200px;height:550px;background:linear-gradient(180deg,#e9edf4,#f6f7fa)}
.test-head{top:60px;width:1200px;text-align:center}
.test-head .eyebrow{font-size:12px}
.test-head h2{font-size:34px;margin-top:6px}
.test-head .rule{margin:6px auto 0}
.quote-card{top:179px;width:434px;height:275px;background:var(--white);border:1px solid #b7c2d4;padding:42px 44px 0 45px}
.stars{color:var(--star);font-size:18px;letter-spacing:2px}
.quote-card p{font-size:13.5px;line-height:24px;color:var(--ink);margin-top:6px}
.quote-card .who{margin-top:18px;font-size:15px;font-weight:600;color:var(--ink);line-height:17px}
.quote-card .who small{display:block;font-size:13px;font-weight:400}
.quote-card .qm{right:30px;bottom:-20px;font-size:110px;color:#c5ccd8;font-weight:800;line-height:1}
.arrow{top:284px}

/* contact */
.contact-left{top:3117px;left:0;width:598px;height:589px;background:var(--navy)}
.contact-right{top:3117px;left:598px;width:602px;height:589px;background:var(--red)}
.contact-left .kicker{left:140px;top:102px;color:var(--white);font-size:19px;font-weight:500}
.contact-left h2{left:137px;top:128px;color:var(--white);font-size:40px;font-weight:800}
.contact-left .rule{left:140px;top:180px;width:70px}
.contact-left .intro{left:135px;top:202px;width:430px;color:#dfe4ee;font-size:13px;line-height:23px}
.info{left:137px;display:flex;align-items:center;gap:16px;color:var(--white);font-size:17px;line-height:21px}
.info b{font-weight:600}
.info .dot{width:38px;height:38px;border-radius:50%;background:var(--white);display:flex;align-items:center;justify-content:center;flex:none}
.contact-right h3{left:107px;top:96px;color:var(--white);font-size:28px;font-weight:800}
.field{background:var(--white);font-size:13px;color:var(--navy);font-weight:500;padding:14px 0 0 24px;border:1px solid #e9dede}
.send{left:107px;top:417px;width:201px;height:50px;background:var(--navy);border-radius:25px;color:var(--white);font-weight:600;font-size:16px;display:flex;align-items:center;justify-content:center;gap:8px}

/* footer */
.footer-badge{left:524px;top:3652px;width:152px;height:163px;background:var(--white);border:5px solid var(--navy);display:flex;flex-direction:column;align-items:center;justify-content:center;gap:8px;text-align:center}
.footer-badge i{width:20px;height:20px;background:var(--red);display:block}
.footer-badge span{color:var(--navy);font-weight:800;font-size:16px;line-height:1.2}
.footer-nav{top:3761px;font-size:14px;font-weight:700;color:var(--navy);white-space:nowrap}
.sep{width:6px;height:6px;background:var(--red);top:3768px}
.hr{left:120px;width:975px;height:1px;background:#c9ccd3}
.foot-info{top:3864px;display:flex;align-items:center;gap:8px;color:var(--navy);font-size:14px;font-weight:500}
.foot-info .dot{width:38px;height:38px;border-radius:50%;background:var(--navy);display:flex;align-items:center;justify-content:center}
.copyright{top:3952px;left:0;width:1200px;text-align:center;font-size:14px;color:var(--muted)}
</style>
</head>
<body>

<header class="site-header abs">
  <nav class="nav abs" style="left:0">
    <a class="active" style="left:396px">HOME</a>
    <a style="left:485px">ABOUT US</a>
    <a style="left:599px">OUR SERVICES</a>
    <a style="left:742px">BLOGS</a>
    <a style="left:834px">CONTACT US</a>
  </nav>
  <div class="phone abs">
    <svg width="16" height="16" viewBox="0 0 24 24"><path fill="#d5252a" d="M6.6 10.8a15.5 15.5 0 0 0 6.6 6.6l2.2-2.2c.3-.3.7-.4 1-.2 1.1.4 2.3.6 3.6.6.6 0 1 .4 1 1V20c0 .6-.4 1-1 1A17 17 0 0 1 3 4c0-.6.4-1 1-1h3.5c.6 0 1 .4 1 1 0 1.3.2 2.5.6 3.6.1.3 0 .7-.2 1z"/></svg>
    614 555 0187
  </div>
</header>
<div class="brand-tag abs"><i class="mark"></i><span>Larkfield Ridge<br>Management</span></div>

<section class="hero abs" role="img" aria-label="Photo of a city skyline at sunset with twin church spires and brick buildings">
  <h1 class="abs">A true partner,<br><b>not just a vendor.</b></h1>
  <p class="abs">Personalized insurance solutions for individuals, families, and businesses. Secure your future with expert guidance you can trust.</p>
  <a class="btn abs">Get a quote <span>↗</span></a>
</section>

<section class="services">
  <div class="services-head abs">
    <div class="eyebrow">What we do</div>
    <h2 class="section-title" style="margin-top:10px">Services provide</h2>
    <div class="rule"></div>
  </div>
  <div class="card card-img abs" style="left:76px" role="img" aria-label="Photo of a hand passing house keys">SERVICE TITLE</div>
  <div class="card featured abs">
    <h3>SERVICE TITLE</h3>
    <p>Lorem ipsum dolor sit amet, consectetur adipiscing elit, sed do eiusmod tempor incididunt ut labore et dolore magna aliqua. Quis ipsum suspendisse ultrices gravida. Risus com</p>
    <a class="btn more">Learn more ↗</a>
  </div>
  <div class="card card-img c3 abs" style="left:606px" role="img" aria-label="Photo of a client meeting in a bright office">SERVICE TITLE</div>
  <div class="card card-img c4 abs" style="left:872px" role="img" aria-label="Photo of a pen beside an architectural building model">SERVICE TITLE</div>
</section>

<section class="about">
  <div class="about-ring abs"></div>
  <div class="about-photo abs" role="img" aria-label="Photo of a couple shaking hands with an agent outside a house"></div>
  <div class="about-eyebrow abs eyebrow">Why we are <i></i></div>
  <h2 class="section-title abs">About Larkfield<br>Ridge Management</h2>
  <div class="rule abs"></div>
  <p class="abs">Our organization delivers comprehensive property management solutions that optimize asset performance and tenant satisfaction. By integrating advanced analytics with proven operational frameworks, our specialists ensure each property achieves sustained value appreciation.</p>
  <a class="btn abs">Who we are <span>↗</span></a>
</section>

<section class="why">
  <div class="why-head abs">
    <div class="eyebrow"><i></i>Why us?<i></i></div>
    <h2 class="section-title">Why choose Larkfield<br>Ridge Management</h2>
    <div class="rule"></div>
  </div>

  <div class="feature left abs" style="left:113px;top:2118px"><h4>Personalized Property<br>Management</h4><p>Lorem ipsum dolor sit amet, consecte-<br>tur adipiscing elit, sed do eiusmod</p></div>
  <div class="icon-box navy abs" style="left:376px;top:2121px"><svg width="40" height="40" viewBox="0 0 40 40" fill="none" stroke="#fff" stroke-width="2"><path d="M6 20 20 8l14 12"/><circle cx="20" cy="23" r="7"/><circle cx="20" cy="23" r="2.5"/></svg></div>

  <div class="feature left abs" style="left:113px;top:2298px"><h4>Responsive<br>Communication</h4><p>Lorem ipsum dolor sit amet, consecte-<br>tur adipiscing elit, sed do eiusmod</p></div>
  <div class="icon-box navy abs" style="left:376px;top:2300px"><svg width="40" height="40" viewBox="0 0 40 40" fill="none" stroke="#fff" stroke-width="2"><circle cx="13" cy="12" r="4"/><circle cx="27" cy="12" r="4"/><path d="M6 26c0-4 3-7 7-7s7 3 7 7M20 26c0-4 3-7 7-7s7 3 7 7"/><rect x="14" y="26" width="12" height="8" rx="2"/></svg></div>

  <div class="divider abs" style="left:135px;top:2252px;width:317px"></div>
  <div class="divider abs" style="left:777px;top:2252px;width:317px"></div>

  <div class="emblem abs"><div class="plate"><i></i><span>Larkfield Ridge<br>Management</span></div></div>

  <div class="icon-box red abs" style="left:783px;top:2121px"><svg width="40" height="40" viewBox="0 0 40 40" fill="none" stroke="#fff" stroke-width="2"><circle cx="13" cy="10" r="4"/><path d="M8 34V20h10v14"/><rect x="22" y="8" width="12" height="12"/><path d="M25 17v-4M28 17v-6M31 17v-3"/></svg></div>
  <div class="feature right abs" style="left:884px;top:2118px"><h4>Professional<br>Oversight</h4><p>Lorem ipsum dolor sit amet, consecte-<br>tur adipiscing elit, sed do eiusmod</p></div>

  <div class="icon-box red abs" style="left:783px;top:2300px"><svg width="40" height="40" viewBox="0 0 40 40" fill="none" stroke="#fff" stroke-width="2"><rect x="8" y="6" width="22" height="20"/><path d="M13 21v-5M18 21v-9M23 21v-6"/><path d="M6 32h14l6-4"/></svg></div>
  <div class="feature right abs" style="left:884px;top:2298px"><h4>Long-Term Value<br>Protection</h4><p>Lorem ipsum dolor sit amet, consecte-<br>tur adipiscing elit, sed do eiusmod</p></div>

  <a class="btn abs">Get inquiry now</a>
</section>

<section class="testimonials abs">
  <div class="test-head abs">
    <div class="eyebrow">Testimonials</div>
    <h2 class="section-title">See what our client says</h2>
    <div class="rule"></div>
  </div>
  <svg class="arrow abs" style="left:98px" width="22" height="40" viewBox="0 0 22 40"><path d="M20 2 2 20l18 18" fill="none" stroke="#5f79a6" stroke-width="2"/></svg>
  <div class="quote-card abs" style="left:166px">
    <div class="stars">★★★★★</div>
    <p>Lorem ipsum dolor sit amet, consectetur adipisc-ing elit, sed do eiusmod tempor incididunt ut labore et dolore magna aliqua. Quis ipsum sus-pendisse ultrices gravida. Risus commodo viverra maecenas accumsan lacus vel facilisis.</p>
    <div class="who">Dalia Morren<small>Verified Customer</small></div>
    <span class="qm abs">”</span>
  </div>
  <div class="quote-card abs" style="left:615px">
    <div class="stars">★★★★★</div>
    <p>Lorem ipsum dolor sit amet, consectetur adipisc-ing elit, sed do eiusmod tempor incididunt ut labore et dolore magna aliqua. Quis ipsum sus-pendisse ultrices gravida. Risus commodo viverra maecenas accumsan lacus vel facilisis.</p>
    <div class="who">Dalia Morren<small>Verified Customer</small></div>
    <span class="qm abs">”</span>
  </div>
  <svg class="arrow abs" style="left:1077px" width="22" height="40" viewBox="0 0 22 40"><path d="M2 2l18 18L2 38" fill="none" stroke="#5f79a6" stroke-width="2"/></svg>
</section>

<section class="contact-left abs">
  <div class="kicker abs">GET IN TOUCH</div>
  <h2 class="abs">CONTACT</h2>
  <div class="rule abs"></div>
  <p class="intro abs">Lorem ipsum dolor sit amet, consectetur adipiscing elit, sed do eiusmod tempor incididunt ut labore et dolore</p>
  <div class="info abs" style="top:298px">
    <span class="dot"><svg width="18" height="18" viewBox="0 0 24 24"><path fill="#1f3461" d="M12 2a7 7 0 0 0-7 7c0 5 7 13 7 13s7-8 7-13a7 7 0 0 0-7-7zm0 9.5A2.5 2.5 0 1 1 12 6.5a2.5 2.5 0 0 1 0 5z"/></svg></span>
    <div>Address<br><b>Maple Hollow &amp; Ridgeview</b></div>
  </div>
  <div class="info abs" style="top:378px">
    <span class="dot"><svg width="18" height="18" viewBox="0 0 24 24" fill="none" stroke="#1f3461" stroke-width="2"><rect x="3" y="5" width="18" height="14" rx="2"/><path d="m3 7 9 6 9-6"/></svg></span>
    <div>Email address<br><b>info@larkfieldridgemanagement.com</b></div>
  </div>
</section>

<section class="contact-right abs">
  <h3 class="abs">SUBMIT INQUIRY</h3>
  <div class="field abs" style="left:111px;top:150px;width:192px;height:45px">First Name</div>
  <div class="field abs" style="left:309px;top:150px;width:198px;height:45px">Last Name</div>
  <div class="field abs" style="left:111px;top:204px;width:396px;height:47px">Email address</div>
  <div class="field abs" style="left:111px;top:258px;width:396px;height:47px">Phone Number</div>
  <div class="field abs" style="left:107px;top:313px;width:400px;height:84px">Leave Message</div>
  <div class="send abs">SEND MESSAGE <span>›</span></div>
</section>

<footer>
  <div class="footer-badge abs"><i></i><span>Larkfield Ridge<br>Management</span></div>
  <div class="footer-nav abs" style="left:127px">HOME</div>
  <span class="sep abs" style="left:193px"></span>
  <div class="footer-nav abs" style="left:218px">ABOUT US</div>
  <span class="sep abs" style="left:317px"></span>
  <div class="footer-nav abs" style="left:345px">SERVICES</div>
  <div class="footer-nav abs" style="left:721px">WHY US</div>
  <span class="sep abs" style="left:801px"></span>
  <div class="footer-nav abs" style="left:828px">CONTACT US</div>
  <span class="sep abs" style="left:944px"></span>
  <div class="footer-nav abs" style="left:973px">GET STARTED</div>

  <div class="hr abs" style="top:3848px"></div>
  <div class="foot-info abs" style="left:128px"><span class="dot"><svg width="18" height="18" viewBox="0 0 24 24"><path fill="#fff" d="M12 2a7 7 0 0 0-7 7c0 5 7 13 7 13s7-8 7-13a7 7 0 0 0-7-7zm0 9.5A2.5 2.5 0 1 1 12 6.5a2.5 2.5 0 0 1 0 5z"/></svg></span>2780 Harrow Lane Columbus OH 43215</div>
  <div class="foot-info abs" style="left:532px"><span class="dot"><svg width="18" height="18" viewBox="0 0 24 24"><path fill="#fff" d="M6.6 10.8a15.5 15.5 0 0 0 6.6 6.6l2.2-2.2c.3-.3.7-.4 1-.2 1.1.4 2.3.6 3.6.6.6 0 1 .4 1 1V20c0 .6-.4 1-1 1A17 17 0 0 1 3 4c0-.6.4-1 1-1h3.5c.6 0 1 .4 1 1 0 1.3.2 2.5.6 3.6.1.3 0 .7-.2 1z"/></svg></span>(614) 555-0142</div>
  <div class="foot-info abs" style="left:782px;font-size:16px"><span class="dot"><svg width="18" height="18" viewBox="0 0 24 24" fill="none" stroke="#fff" stroke-width="2"><rect x="3" y="5" width="18" height="14" rx="2"/><path d="m3 7 9 6 9-6"/></svg></span>info@larkfieldridgemanagement.com</div>
  <div class="hr abs" style="top:3925px"></div>
  <div class="copyright abs">Copyright © 2026 Larkfield Ridge Management LLC</div>
</footer>

</body>
</html>
```